Business Card Design for Marketing Firm

Looking for business card design for higher end marketing firm. Clean but impressionable/trendy. We are a marketing firm that represents manufacturers in the foodservice equipment and supply industry. Our customers are end users such has hotels, restaurants, country clubs, convention centers and casinos as well as distributors of restaurants supplies and equipment, and manufacturers of foodservice equipment and supplies.
Target Market(s)
Hotels, Restaurants, Supply & Equipment Distributors, Foodservice Manufacturers
Industry/Entity Type
Foodservice/Hospitality
Contact Information for Business Card
Name, Title, Contact Number, Email, Website, Social Media, Address
Requirements
Must have
- Clean & Simple but Serious and Impressionable

```html
<!DOCTYPE html>
<html lang="en">
<head>
<meta charset="utf-8">
<title>Meridian Hospitality Reps – Business Cards</title>
<link href="https://fonts.googleapis.com/css2?family=Montserrat:wght@400;500;700&display=swap" rel="stylesheet">
<style>
  :root {
    --navy: #28287a;
    --white: #ffffff;
    --page: #ecebe8;
    --ink: #2b2b3a;
  }
  * { margin: 0; padding: 0; box-sizing: border-box; }
  html, body { width: 1200px; height: 834px; overflow: hidden; }
  body {
    background: var(--page);
    font-family: "Montserrat", sans-serif;
    display: flex;
    align-items: center;
    justify-content: center;
    gap: 40px;
  }
  .card {
    position: relative;
    width: 540px;
    height: 309px;
    background: var(--white);
    box-shadow: 0 6px 18px rgba(0,0,0,.18);
    overflow: hidden;
  }
  /* contact side */
  .card-wave { position: absolute; inset: 0; width: 100%; height: 100%; }
  .name-block {
    position: absolute; top: 20px; left: 0;
    display: flex; align-items: flex-start; gap: 12px;
  }
  .name-bar { width: 14px; height: 36px; background: var(--navy); }
  .person-name {
    font-weight: 700; font-size: 19px; letter-spacing: .5px;
    color: var(--navy); line-height: 1.05;
  }
  .person-title { font-size: 12px; color: var(--ink); margin-top: 3px; }
  .contact-list {
    position: absolute; left: 26px; top: 112px;
    list-style: none; color: var(--white); font-size: 13px; line-height: 1.45;
  }
  .contact-list .address { margin-bottom: 10px; }
  .contact-list li { display: flex; align-items: center; gap: 8px; }
  .contact-list .address { display: block; padding-left: 20px; }
  .icon { width: 12px; height: 12px; flex: none; }
  .brand-name {
    font-weight: 500; color: var(--navy);
    text-transform: uppercase; letter-spacing: 1.5px; line-height: 1.2;
  }
  .contact-card .brand-name {
    position: absolute; right: 34px; top: 170px;
    font-size: 15px; text-align: right;
  }
  /* logo side */
  .logo-card {
    display: flex; flex-direction: column; align-items: center; justify-content: center; gap: 26px;
  }
  .logo-card .brand-name { font-size: 26px; text-align: center; }
  .social-row { display: flex; gap: 8px; }
  .social-dot { width: 16px; height: 16px; border-radius: 50%; background: var(--navy); }
</style>
</head>
<body>
  <section class="card contact-card">
    <svg class="card-wave" viewBox="0 0 540 309" preserveAspectRatio="none" aria-hidden="true">
      <path d="M0 88 C 120 82, 190 120, 250 200 C 300 265, 360 305, 420 309 L 0 309 Z" fill="var(--navy)"/>
      <path d="M20 84 C 130 84, 200 122, 262 202 C 312 266, 372 300, 430 309" fill="none" stroke="var(--white)" stroke-width="3"/>
      <path d="M24 82 C 135 84, 210 122, 272 202 C 322 266, 382 298, 440 309" fill="none" stroke="var(--navy)" stroke-width="2"/>
    </svg>
    <div class="name-block">
      <div class="name-bar"></div>
      <div>
        <div class="person-name">DANIEL REYES</div>
        <div class="person-title">Managing Director</div>
      </div>
    </div>
    <ul class="contact-list">
      <li class="address">Your address, City<br>State, Zip 1234</li>
      <li>
        <svg class="icon" viewBox="0 0 12 12"><path d="M2 1h3l1 3-2 1a7 7 0 0 0 3 3l1-2 3 1v3a1 1 0 0 1-1 1A10 10 0 0 1 1 2a1 1 0 0 1 1-1z" fill="var(--white)"/></svg>
        123 456 789
      </li>
      <li>
        <svg class="icon" viewBox="0 0 12 12"><rect x="0.5" y="2" width="11" height="8" fill="var(--white)"/><path d="M0.5 2l5.5 4.5L11.5 2" fill="none" stroke="var(--navy)"/></svg>
        info@yourmail.com
      </li>
      <li>
        <svg class="icon" viewBox="0 0 12 12"><circle cx="6" cy="6" r="5.5" fill="var(--white)"/><path d="M0.5 6h11M6 .5c-3 3-3 8 0 11M6 .5c3 3 3 8 0 11" fill="none" stroke="var(--navy)" stroke-width=".8"/></svg>
        www.yourwebsite.com
      </li>
    </ul>
    <div class="brand-name">Meridian Hospitality<br>Reps</div>
  </section>

  <section class="card logo-card">
    <div class="brand-name">Meridian Hospitality<br>Reps</div>
    <div class="social-row" aria-label="Social media">
      <span class="social-dot"></span><span class="social-dot"></span><span class="social-dot"></span>
      <span class="social-dot"></span><span class="social-dot"></span><span class="social-dot"></span>
    </div>
  </section>
</body>
</html>
```